Design a label for a dog shampoo names fluffo, the sell point of this series of shampoo is “just like wash your dogs with milk, not harm for your hand ”, the style could be gentle or professional or even amazing.

Use only 2 colors in the design job, the color of our logo could be changed, it depends on your whole page. Please design in CDR or ai.

update:
Pls do more change with the fonts when you design the front page, including title and details. Try more styles of fonts. Addition, this design will be printed on the bottle, no a label stick on it.
Updates

Do not put a real dog or animal on the page, Pay more attention to the types of fonts

Reason: Expect for more design idea.

Target Market(s)

people 20-30 years old who have dogs and cats at home

Industry/Entity Type

It Professional

Requirements
Nice to have
• It would be nice if you add some detail words in the design of the right side.

```html
<!DOCTYPE html>
<html lang="en">
<head>
<meta charset="utf-8">
<title>fluffo Milk Shampoo – Bottle Print</title>
<link rel="stylesheet" href="https://fonts.googleapis.com/css2?family=Roboto+Condensed:wght@400;700&family=Ultra&family=Oswald:wght@500;600&display=swap">
<style>
  :root{
    --teal:#1fa3b6;
    --pink:#f6a8dc;
    --pink-deep:#e586c6;
    --print-base:#f7f6f1;
    --stage:#d9d9d9;
    --ink-white:#ffffff;
  }
  *{box-sizing:border-box;margin:0;padding:0}
  html,body{width:1200px;height:1200px;overflow:hidden}
  body{background:var(--stage);font-family:"Roboto Condensed",Arial,sans-serif;display:flex;align-items:center;justify-content:center;gap:60px}
  .print-face{width:500px;height:860px;background:var(--print-base);border-radius:40px;position:relative;display:flex;flex-direction:column;align-items:center}

  /* front */
  .front{padding-top:70px}
  .brand{display:flex;align-items:center;gap:12px;color:var(--teal);font-family:"Oswald",sans-serif;font-weight:600;font-size:62px;line-height:1;letter-spacing:1px}
  .brand-dot{width:18px;height:18px;border-radius:50%;background:var(--teal)}
  .front-panel{position:relative;margin-top:30px;width:400px;height:600px}
  .ornament{position:absolute;inset:0;border-radius:30px;background:radial-gradient(ellipse at center,rgba(31,163,182,.10),rgba(31,163,182,.28))}
  .pink-field{position:absolute;inset:22px 34px;background:var(--pink);border-radius:24px;border:3px solid var(--teal);display:flex;flex-direction:column;align-items:center;justify-content:center;text-align:center}
  .claim{font-family:"Oswald",sans-serif;font-weight:500;color:var(--ink-white);font-size:24px;line-height:1.15;letter-spacing:.5px}
  .product-type{font-family:"Oswald",sans-serif;font-weight:600;color:var(--teal);font-size:40px;margin-top:6px;letter-spacing:1px}
  .product-name{font-family:"Ultra",serif;color:var(--ink-white);font-size:92px;line-height:1;margin:34px 0 38px}
  .benefit{font-family:"Oswald",sans-serif;font-weight:500;color:var(--ink-white);font-size:26px;line-height:1.15}
  .volume{margin-top:38px;background:var(--teal);color:var(--ink-white);font-family:"Oswald",sans-serif;font-weight:600;font-size:24px;padding:4px 22px;border-radius:6px}

  /* back */
  .back{padding:80px 40px 0;color:var(--teal)}
  .back .brand{font-size:40px;margin-bottom:26px}
  .back-title{font-weight:700;font-size:26px;align-self:flex-start}
  .back-intro{font-size:14px;line-height:1.35;margin-top:8px}
  .directions{margin-top:20px;width:100%;border:2px solid var(--teal);border-radius:10px;padding:22px 16px 12px;position:relative}
  .directions-tag{position:absolute;top:-14px;left:50%;transform:translateX(-50%);background:var(--pink);color:var(--ink-white);font-weight:700;font-size:16px;padding:2px 24px;border-radius:12px;letter-spacing:1px}
  .directions ol{list-style:none;font-size:13px;line-height:1.5}
  .section-head{margin-top:20px;color:var(--pink-deep);font-weight:700;font-size:16px;text-decoration:underline}
  .section-text{font-size:14px;line-height:1.35;margin-top:6px;align-self:stretch}
  .centered{text-align:center}
</style>
</head>
<body>
  <section class="print-face front">
    <div class="brand"><span>fluffo</span><span class="brand-dot"></span></div>
    <div class="front-panel">
      <div class="ornament" role="img" aria-label="Teal ornamental scrollwork framing the pink panel"></div>
      <div class="pink-field">
        <p class="claim">SUPER-CONDITIONING<br>AND NUTRIENT</p>
        <p class="product-type">SHAMPOO</p>
        <p class="product-name">MILK</p>
        <p class="benefit">MOISTURE-RICH<br>SMOOTH AND SILKY</p>
        <p class="volume">1000 ml</p>
      </div>
    </div>
  </section>

  <section class="print-face back">
    <div class="brand"><span>fluffo</span><span class="brand-dot"></span></div>
    <h2 class="back-title">Super-Conditioning &amp; Nutrient Shampoo</h2>
    <p class="back-intro">is a specially formulated shampoo, rich in conditioners picked up from milk which subdivide and balance nutrition of pet's coat. More easier and better assimilate for coat from base to the end after using. With the help of minus-ion, the balancer of nutrition, rinses out quickly and completely to leave a soft, sparkling, and smooth coat. Safe and gentle enough to be used every day. Safe for even the most sensitive skin and coat, puppies, lactating bitches and cats.</p>
    <div class="directions">
      <span class="directions-tag">DIRECTIONS</span>
      <ol>
        <li>a) Before shampooing, brush out pet's coat.</li>
        <li>b) Saturate dog's coat with lukewarm water.</li>
        <li>c) Dispense a small amount of shampoo into the palm of your hand.</li>
        <li>d) To clean coat, start at dog's head and work back towards the tail.</li>
        <li>e) Avoid getting shampoo into the dog's eyes and ears.</li>
        <li>f) Rinse coat several times with lukewarm water.</li>
        <li>g) Towel dry and gently comb or brush coat.</li>
      </ol>
    </div>
    <h3 class="section-head">ACTIVE INGREDIENTS:</h3>
    <p class="section-text centered">Hypochlorous Acid, Sodium Hypochlorite</p>
    <h3 class="section-head">USE PRECAUTIONS:</h3>
    <p class="section-text">Harmful if swallowed. Do not inhale. Discontinue use if irritation develops and contact your veterinarian. For animal use only. Not for human use. Keep out of reach of children. Do not decant into smaller containers. Not for injection. Always consult with a Veterinarian for systemic conditions.</p>
    <h3 class="section-head">STORAGE AND DISPOSAL</h3>
    <p class="section-text">Keep out of the reach of children. Replace Cap. Wrap in several layers of newspaper and discard in trash.</p>
  </section>
</body>
</html>
```